PlayTallyCollective - Game Statistics and Achievement Tracking

I need a new modern design for an existing website.

The website is a project to track statistics and achievements for games (currently Vaporn Achievements/Stats and stats for Cargo Haul Odyssey 2 and Frontier Rig Journeys).
I am currently expanding the site with other platforms (like QVR) and more games.
I am also adding a user registration/signin with user profiles to show off their achievements and stats across all platforms and games.

The current website is available at https://plytly.example/
To search for data you can use the username "pixelornin" (without quotes).

The design should be modern and extendable and contain space for a logo.

The logo should match the project. It should combine Gaming with statistics.

Target Market(s)

Video game players

Number of Pages Required

5+ page

Font styles to use
Sans Serif

Requirements
Must have
• Basic Layout, User profile page (not yet available on live site), Search Page for Platforms/Games, Platform profile page, Dark theme

```html
<!DOCTYPE html>
<html lang="en">
<head>
<meta charset="utf-8">
<title>PlayTally Collective – Game Statistics</title>
<link href="https://fonts.googleapis.com/css2?family=Anton&family=Mulish:wght@400;500;600;700;800&display=swap" rel="stylesheet">
<style>
:root{
  --bg:#0f1215;
  --bg-deep:#0a0c0e;
  --panel:#1a1f1d;
  --green:#45e86f;
  --yellow:#fbbd18;
  --white:#ffffff;
  --muted:#c9ccd0;
  --row-alt:#231f14;
  --ink:#121212;
}
*{box-sizing:border-box;margin:0;padding:0}
html,body{width:1200px;height:4185px;overflow:hidden}
body{position:relative;background:linear-gradient(180deg,#1b2023 0%,#12161a 18%,#0f1215 30%,#15191c 45%,#101316 70%,#0c0f12 100%);font-family:"Mulish",sans-serif;color:var(--white)}
.abs{position:absolute}
.display{font-family:"Anton",sans-serif;font-weight:400;text-transform:uppercase;letter-spacing:.5px}
.accent{color:var(--yellow)}
.btn{position:absolute;display:flex;align-items:center;justify-content:center;border-radius:24px;background:linear-gradient(90deg,var(--yellow),#e9d21a 60%,var(--green));color:var(--ink);font-size:14px;font-weight:600;text-transform:uppercase}
.btn-solid{background:var(--yellow)}

.top-line{left:0;top:0;width:1200px;height:3px;background:var(--green)}
.topbar{left:110px;top:22px;width:980px;height:22px;display:flex;align-items:center;font-size:12px;font-weight:700}
.topbar .lang{display:flex;align-items:center;gap:6px;font-size:15px;font-weight:600}
.social-links{margin-left:auto;display:flex;align-items:center}
.social-links span{padding:0 28px}
.social-links .sep{padding:0;opacity:.8}
.login{color:var(--yellow);margin-left:30px;font-size:13px}
.dot{width:10px;height:10px;border-radius:50%;background:var(--green);display:inline-block}

.brand{display:flex;align-items:center;gap:12px}
.brand .mark{width:56px;height:56px;border-radius:50%;background:radial-gradient(circle at 40% 35%,var(--yellow),var(--green) 70%)}
.brand .name{font-family:"Anton",sans-serif;font-size:28px;color:var(--yellow);line-height:1}
.mainnav{left:440px;top:104px;display:flex;gap:38px;font-size:14px;font-weight:500}
.mainnav .active{color:var(--yellow)}

.hero-tag{left:0;width:1200px;top:198px;text-align:center;color:var(--green);font-size:17px;font-weight:600}
.hero-title{left:0;width:1200px;top:230px;text-align:center;font-size:46px}
.hero-copy{left:300px;width:600px;top:294px;text-align:center;font-size:15px;line-height:27px}

.card-shape{left:0;top:0}
.avatar{left:175px;top:528px;width:351px;height:334px;background:linear-gradient(140deg,#f5e9d0,#c99a5a 45%,#3e6fb8);clip-path:polygon(0 0,94% 0,100% 8%,100% 100%,6% 100%,0 94%)}
.location{left:235px;top:805px;width:291px;height:57px;background:var(--yellow);color:var(--ink);font-size:15px;font-weight:500;display:flex;align-items:center;justify-content:center;clip-path:polygon(8% 0,100% 0,100% 100%,0 100%)}
.facts{left:576px;top:524px;font-size:14px}
.fact{display:flex;align-items:center;height:42px}
.fact i{width:16px;height:16px;border-radius:4px;background:var(--green);margin-right:14px}
.fact b{width:146px;font-weight:800;text-transform:uppercase}
.fact .colon{width:24px}
.fact .val{font-weight:500}
.mini-stats{left:560px;top:792px;display:flex}
.mini-stats div{width:115px;text-align:center}
.mini-stats strong{display:block;font-size:24px;font-weight:700}
.mini-stats span{display:block;font-size:13px;margin-top:10px}

.search-band{left:0;top:879px;width:1200px;height:276px;background:var(--green)}
.search-title{left:110px;top:988px;color:var(--ink);font-size:46px}
.search-input{left:516px;top:990px;width:394px;height:54px;border-radius:28px;background:var(--ink);display:flex;align-items:center;padding-left:32px;font-size:15px;gap:14px}
.search-btn{left:926px;top:990px;width:160px;height:54px;font-size:15px;text-transform:none;font-weight:600}
.search-copy{left:240px;width:720px;top:1066px;text-align:center;color:var(--ink);font-size:15px;line-height:28px}

.history-img{left:110px;top:1271px;width:502px;height:386px;border:1px solid var(--yellow);background:linear-gradient(135deg,#0d2a44,#1c5d8c 50%,#0a1826)}
.history-title{left:676px;top:1300px;font-size:46px}
.history-copy{left:676px;top:1372px;width:420px;font-size:15px;line-height:30px}
.history-btn{left:676px;top:1578px;width:138px;height:42px}

.section-title{left:0;width:1200px;text-align:center;font-size:46px}
.section-copy{left:220px;width:760px;text-align:center;font-size:15px;line-height:31px}

.stat-card{width:227px;height:184px;border-radius:14px;background:linear-gradient(160deg,#2a3226,#15191b 70%);text-align:center;padding-top:26px}
.stat-card.highlight{border:1px solid var(--green)}
.stat-card .ic{width:72px;height:72px;border-radius:50%;margin:0 auto;background:linear-gradient(135deg,var(--yellow),var(--green));display:flex;align-items:center;justify-content:center}
.stat-card strong{display:block;font-size:25px;font-weight:800;margin-top:16px}
.stat-card span{display:block;font-size:13px;margin-top:4px}

.stats-table{left:110px;top:2475px;width:978px;border-collapse:collapse;font-size:17px}
.stats-table th{background:var(--yellow);color:var(--ink);height:70px;text-align:left;font-weight:600;font-size:18px}
.stats-table td{height:72px;vertical-align:middle}
.stats-table tbody tr:nth-child(even){background:var(--row-alt)}
.stats-table tbody tr:first-child td{height:211px;vertical-align:top;padding-top:28px}
.col-check{width:97px;padding-left:40px}
.box{display:inline-block;width:17px;height:17px;border:1.5px solid var(--white)}
.box.filled{background:var(--white)}
th .box.filled{background:var(--ink);border-color:var(--ink)}
.col-game{width:233px}
.col-time{width:224px}
.col-played{width:187px}
.game-name{font-weight:600}
.thumb{width:156px;height:98px;margin-top:18px;background:linear-gradient(135deg,#7a5ca8,#b58fd0 55%,#2a1d44)}
.bar{width:210px;height:14px;border-radius:7px;background:var(--green);position:relative}
.bar em{position:absolute;right:10px;top:2px;font-size:7px;font-style:normal;color:var(--ink)}

.user{width:231px;text-align:center}
.user .pic{height:263px;border-radius:8px}
.user span{display:block;font-size:15px;font-weight:700;margin-top:24px}

.footer-brand{left:428px;top:3912px}
.footer-brand .mark{width:78px;height:78px}
.footer-brand .name{font-size:40px}
.footer-nav{left:0;width:1200px;top:4024px;display:flex;justify-content:center;gap:48px;font-size:16px;font-weight:500}
.footer-social{left:0;width:1200px;top:4072px;display:flex;justify-content:center;gap:22px}
.footer-social span{width:38px;height:38px;border-radius:50%;background:var(--green);display:flex;align-items:center;justify-content:center}
.footer-social i{width:10px;height:10px;background:var(--ink);border-radius:2px}
.copyright{left:0;width:1200px;top:4146px;text-align:center;font-size:11px}
</style>
</head>
<body>

<div class="abs top-line"></div>
<div class="abs topbar">
  <div class="lang"><span class="dot"></span>Language ▾</div>
  <nav class="social-links">
    <span>FriendHub</span><span class="sep">|</span>
    <span>Chirpline</span><span class="sep">|</span>
    <span>ViewStream</span><span class="sep">|</span>
    <span>SnapGallery</span>
  </nav>
  <span class="login">🔒 Login</span>
</div>

<header>
  <div class="abs brand" style="left:110px;top:84px">
    <span class="mark"></span>
    <span class="name">PlayTally Collective</span>
  </div>
  <nav class="abs mainnav">
    <span class="active">HOME</span><span>ABOUT US</span><span>STREAM</span><span>GAMES</span><span>CONTACT US</span>
  </nav>
  <div class="btn btn-solid" style="left:931px;top:92px;width:158px;height:42px">Register Here</div>
</header>

<section class="hero">
  <p class="abs hero-tag">Get the Data. Own the Game</p>
  <h1 class="abs hero-title display">Unleash the power of data in gaming!</h1>
  <p class="abs hero-copy">Welcome to the PlayTally Collective! We offer you free and easy insights into your game statistics and achievements on multiple platforms and games.</p>
  <div class="btn" style="left:431px;top:369px;width:158px;height:42px">Register Here</div>
  <div class="btn" style="left:611px;top:369px;width:158px;height:42px">Get in Touch</div>
</section>

<div class="abs search-band"></div>

<section class="profile">
  <svg class="abs card-shape" width="1200" height="940" viewBox="0 0 1200 940">
    <polygon points="130,460 1022,460 1070,510 1070,930 200,930 130,872" fill="#0b0d0f" stroke="#45e86f" stroke-width="1.5"/>
    <polyline points="1022,460 1070,510 1070,560" fill="none" stroke="#fbbd18" stroke-width="2"/>
  </svg>
  <div class="abs avatar" role="img" aria-label="Cartoon profile avatar of the player"></div>
  <div class="abs location">Nordrhein-Westfalen, Germany</div>
  <div class="abs facts">
    <div class="fact"><i></i><b>Played Games</b><span class="colon">:</span><span class="val">1166 / 1644 (70%)</span></div>
    <div class="fact"><i></i><b>Total Play Time</b><span class="colon">:</span><span class="val">1 year 2 months 11 hours 25 minutes</span></div>
    <div class="fact"><i></i><b>Achievements</b><span class="colon">:</span><span class="val">18007 / 63070 (28%)</span></div>
    <div class="fact"><i></i><b>Member Since</b><span class="colon">:</span><span class="val">14.01.2009</span></div>
    <div class="fact"><i></i><b>Last Played</b><span class="colon">:</span><span class="val">Rail Driver Realm 5</span></div>
    <div class="fact"><i></i><b>Last Update</b><span class="colon">:</span><span class="val">26.12.2024 11:20h</span></div>
  </div>
  <div class="abs mini-stats">
    <div><strong>179</strong><span>Vaporn Level</span></div>
    <div><strong>15</strong><span>Account Age</span></div>
    <div><strong>87</strong><span>Perfect Games</span></div>
  </div>
</section>

<section class="search">
  <h2 class="abs search-title display">Search Vaporn User</h2>
  <div class="abs search-input"><span>👤</span><span>|</span><span>Vaporn ID</span></div>
  <div class="btn btn-solid search-btn">Search Here</div>
  <p class="abs search-copy">Sed ut perspiciatis unde omnis iste natus error sit voluptatem accusantium doloremque laudantium, totam rem aperiam, eaque ipsa quae ab illo inventore veritatis et</p>
</section>

<section class="history">
  <div class="abs history-img" role="img" aria-label="Analyst studying data on several monitors at night"></div>
  <h2 class="abs history-title display">Our <span class="accent">History</span></h2>
  <p class="abs history-copy">The PlayTally Collective, short PTally or P-Tally, was established in August 2012 as a website providing game statistics for the Syndicate 2 Multiplayer Modification, that was work in progress back in the date and has sadly been canceled some years later, and Blockcraft with a custom Blockkit plugin.</p>
  <div class="btn history-btn">Read More</div>
</section>

<section class="user-stats">
  <h2 class="abs section-title display" style="top:1752px">User <span class="accent">Statistics</span></h2>
  <p class="abs section-copy" style="top:1822px">After the Syndicate 2 Multiplayer Modification had been cancelled and Blockkit has been shutdown the network moved on to provide game time and achievement statistics for Vaporn.</p>
  <div class="abs stat-card" style="left:112px;top:1918px"><div class="ic"><svg width="30" height="20"><rect x="1" y="3" width="28" height="14" rx="7" fill="#121212"/></svg></div><strong>251966</strong><span>Games</span></div>
  <div class="abs stat-card highlight" style="left:362px;top:1918px"><div class="ic"><svg width="26" height="28"><path d="M4 2h18v8a9 9 0 0 1-18 0z M11 19h4v5h5v3H6v-3h5z" fill="#121212"/></svg></div><strong>2692707</strong><span>Game Achievements</span></div>
  <div class="abs stat-card" style="left:611px;top:1918px"><div class="ic"><svg width="24" height="28"><path d="M2 3h20v10c0 7-10 13-10 13S2 20 2 13z" fill="#121212"/></svg></div><strong>339284</strong><span>Game Stats</span></div>
  <div class="abs stat-card" style="left:861px;top:1918px"><div class="ic"><svg width="30" height="24"><path d="M1 3h10l3 3h15v16H1z" fill="#121212"/></svg></div><strong>3271530</strong><span>Playtime Records</span></div>
  <div class="abs stat-card" style="left:112px;top:2136px"><div class="ic"><svg width="32" height="24"><circle cx="16" cy="7" r="6" fill="#121212"/><circle cx="6" cy="9" r="4" fill="#121212"/><circle cx="26" cy="9" r="4" fill="#121212"/><rect x="6" y="14" width="20" height="9" rx="4" fill="#121212"/></svg></div><strong>1033</strong><span>Public Profiles</span></div>
  <div class="abs stat-card" style="left:362px;top:2136px"><div class="ic"><svg width="24" height="28"><circle cx="12" cy="8" r="7" fill="#121212"/><rect x="1" y="16" width="22" height="11" rx="5" fill="#121212"/></svg></div><strong>21087125</strong><span>User Achievements</span></div>
  <div class="abs stat-card" style="left:611px;top:2136px"><div class="ic"><svg width="30" height="30"><path d="M2 2h13l13 13-13 13L2 15z" fill="#121212"/></svg></div><strong>2552885</strong><span>User Stats</span></div>
  <div class="abs stat-card" style="left:861px;top:2136px"><div class="ic"><svg width="28" height="28"><circle cx="14" cy="14" r="8" fill="none" stroke="#121212" stroke-width="3"/><path d="M14 0v8M14 20v8M0 14h8M20 14h8" stroke="#121212" stroke-width="3"/></svg></div><strong>2276964</strong><span>Owned Games</span></div>
</section>

<table class="abs stats-table">
  <thead>
    <tr><th class="col-check"><span class="box filled"></span></th><th class="col-game">Game Details</th><th class="col-time">Played Time</th><th class="col-played">Played Games</th><th>Game Process</th></tr>
  </thead>
  <tbody>
    <tr><td class="col-check"><span class="box filled"></span></td><td><div class="game-name">Toward the Stars</div><div class="thumb" role="img" aria-label="Game cover artwork"></div></td><td>5 Hours</td><td>01/01</td><td><div class="bar"><em>100%</em></div></td></tr>
    <tr><td class="col-check"><span class="box"></span></td><td class="game-name">Leave the Chamber</td><td>1 hour 31 minutes</td><td>03/03</td><td><div class="bar"><em>100%</em></div></td></tr>
    <tr><td class="col-check"><span class="box"></span></td><td class="game-name">logicWEAVE</td><td>27 minutes</td><td>05/05</td><td><div class="bar"><em>100%</em></div></td></tr>
    <tr><td class="col-check"><span class="box"></span></td><td class="game-name">Wicked 2 "Quick Demo"</td><td>36 minutes</td><td>06/06</td><td><div class="bar"><em>100%</em></div></td></tr>
    <tr><td class="col-check"><span class="box"></span></td><td class="game-name">Flight2091</td><td>43 minutes</td><td>06/06</td><td><div class="bar"><em>100%</em></div></td></tr>
    <tr><td class="col-check"><span class="box"></span></td><td class="game-name">Petit Domaine</td><td>59 minutes</td><td>07/07</td><td><div class="bar"><em>100%</em></div></td></tr>
  </tbody>
</table>
<div class="btn" style="left:531px;top:3157px;width:138px;height:42px">Load More</div>

<section class="users">
  <h2 class="abs section-title display" style="top:3276px">Our <span class="accent">Users</span></h2>
  <p class="abs section-copy" style="top:3347px">After the Syndicate 2 Multiplayer Modification had been cancelled and Blockkit has been shutdown the network moved on to provide game time and achievement statistics for Vaporn.</p>
  <div class="abs user" style="left:111px;top:3448px"><div class="pic" role="img" aria-label="Anime-style user avatar" style="background:linear-gradient(160deg,#f4c6d8,#8c6bb0)"></div><span>@mirela 481203</span></div>
  <div class="abs user" style="left:360px;top:3448px"><div class="pic" role="img" aria-label="Anime-style user avatar" style="background:linear-gradient(160deg,#2d4fb0,#d89a6a)"></div><span>@tessa 9021</span></div>
  <div class="abs user" style="left:609px;top:3448px"><div class="pic" role="img" aria-label="Cartoon gamer user avatar" style="background:linear-gradient(160deg,#3a7fd8,#1a3f8a)"></div><span>@brandt 6187</span></div>
  <div class="abs user" style="left:858px;top:3448px"><div class="pic" role="img" aria-label="Retro city action user avatar" style="background:linear-gradient(180deg,#e2573a,#7a2a6e 60%,#111)"></div><span>@mirela 481203</span></div>
  <div class="btn" style="left:531px;top:3784px;width:204px;height:42px">Load More Users</div>
</section>

<footer>
  <div class="abs brand footer-brand"><span class="mark"></span><span class="name">PlayTally Collective</span></div>
  <nav class="abs footer-nav"><span>HOME</span><span>ABOUT US</span><span>STREAM</span><span>GAMES</span><span>CONTACT US</span></nav>
  <div class="abs footer-social"><span><i></i></span><span><i></i></span><span><i></i></span></div>
  <p class="abs copyright">(C) Copyright 2024 | All Rights Reserved</p>
</footer>

</body>
</html>
```